Business card for builder specialising in renovations.

Need a card for our building business. Business name is under Martin Powles.
Have licence number on card ( 527691K)
Contact number (0400 382 415)
Want to work on logo for some business cards and shirts - something with MP or MPB or open to ideas??
No animations, No hammers. Something sharp and eye catching.
Highlight that we are a renovation specialist. Simple on front with extra details on back with some lines to jot down things.

Target Market(s)

Renovators

Industry/Entity Type

Building

Contact Information for Business Card

2 sided with room on back to jot things down.
Extra details on back so front can be simple ..like, renovations, bathrooms, decks, extensions, new builds,

Logo Text

MP

Font styles to use
Serif

Requirements
Must have
• Eye catching design .
• Name : Martin powles
• Licence number
• Contact number - 0400382415
Nice to have
• Some logo design that we can carry through to other forms of advertising
• Local builder
• Quality work
Should not have
• No animations

```html
<!DOCTYPE html>
<html lang="en">
<head>
<meta charset="utf-8">
<title>Martin Powles – Business Card</title>
<link rel="stylesheet" href="https://fonts.googleapis.com/css2?family=PT+Serif:wght@400;700&display=swap">
<style>
  :root {
    --canvas: #e6e6e6;
    --ink: #0a0a0a;
    --paper: #ffffff;
    --accent: #26a9e0;
    --text-dark: #1a1a1a;
  }
  * { box-sizing: border-box; margin: 0; padding: 0; }
  html, body { width: 1200px; height: 900px; overflow: hidden; }
  body {
    background: var(--canvas);
    font-family: "PT Serif", Georgia, serif;
    position: relative;
  }
  .card {
    position: absolute;
    left: 250px;
    width: 700px;
    height: 400px;
    overflow: hidden;
  }
  .card--back { top: 35px; background: var(--ink); color: var(--paper); }
  .card--front { top: 465px; background: var(--paper); color: var(--text-dark); }

  /* Back side */
  .services {
    position: absolute;
    left: 80px;
    top: 250px;
    list-style: none;
  }
  .services li {
    display: flex;
    align-items: center;
    gap: 12px;
    font-size: 17px;
    letter-spacing: 0.5px;
    line-height: 26px;
    text-transform: uppercase;
  }
  .services li::before {
    content: "";
    width: 11px;
    height: 11px;
    background: var(--accent);
  }
  .brand-back {
    position: absolute;
    left: 420px;
    top: 150px;
    text-align: center;
  }
  .brand-name {
    display: flex;
    align-items: center;
    gap: 12px;
    font-size: 26px;
    font-weight: 700;
    text-transform: uppercase;
    letter-spacing: 0.5px;
  }
  .brand-mark { width: 30px; height: 30px; background: var(--accent); flex: none; }
  .brand-back .brand-name { color: var(--paper); }
  .web { font-size: 18px; margin-top: 8px; }
  .web .hl { color: var(--accent); }

  /* Front side */
  .rule {
    position: absolute;
    left: 0; right: 0;
    top: 232px;
    height: 2px;
    background: var(--accent);
  }
  .brand-front {
    position: absolute;
    left: 60px;
    top: 186px;
  }
  .brand-front .brand-name { color: var(--text-dark); }
  .contact {
    position: absolute;
    left: 445px;
    top: 192px;
  }
  .contact-name {
    color: var(--accent);
    font-size: 24px;
    text-transform: uppercase;
    line-height: 36px;
  }
  .contact-role { font-size: 15px; margin-top: 6px; }
  .contact-list { list-style: none; margin-top: 2px; }
  .contact-list li {
    display: flex;
    align-items: center;
    gap: 8px;
    font-size: 15px;
    line-height: 21px;
  }
  .label { color: var(--accent); }
  .icon { width: 12px; height: 12px; flex: none; }
</style>
</head>
<body>

<section class="card card--back" aria-label="Card back">
  <ul class="services">
    <li>Renovations</li>
    <li>Bathrooms Decks</li>
    <li>Extensions</li>
    <li>New Builds</li>
  </ul>
  <div class="brand-back">
    <div class="brand-name"><span class="brand-mark"></span>Martin Powles</div>
    <p class="web">www.<span class="hl">martinpowles</span>.com</p>
  </div>
</section>

<section class="card card--front" aria-label="Card front">
  <div class="rule"></div>
  <div class="brand-front">
    <div class="brand-name"><span class="brand-mark"></span>Martin Powles</div>
  </div>
  <div class="contact">
    <p class="contact-name">Martin Powles</p>
    <p class="contact-role">Director</p>
    <ul class="contact-list">
      <li><span class="label">Licence:</span> (527691K)</li>
      <li>
        <svg class="icon" viewBox="0 0 12 12"><path d="M2.5 1l2 2.2-1 1.3a7 7 0 0 0 4 4l1.3-1L11 9.5 9.8 11C5 10.5 1.5 7 1 2.2z" fill="#26a9e0"/></svg>
        0400382415
      </li>
      <li>
        <svg class="icon" viewBox="0 0 12 12"><rect x="1" y="2.5" width="10" height="7" fill="none" stroke="#26a9e0" stroke-width="1.2"/><path d="M1 2.8l5 3.6 5-3.6" fill="none" stroke="#26a9e0" stroke-width="1.2"/></svg>
        info@martinpowles.com
      </li>
      <li>
        <svg class="icon" viewBox="0 0 12 12"><circle cx="6" cy="6" r="5" fill="none" stroke="#26a9e0" stroke-width="1.1"/><ellipse cx="6" cy="6" rx="2.2" ry="5" fill="none" stroke="#26a9e0" stroke-width="1"/><path d="M1 6h10" stroke="#26a9e0" stroke-width="1"/></svg>
        www.<span class="label">martinpowles</span>.com
      </li>
    </ul>
  </div>
</section>

</body>
</html>
```